Boutique custom software development company needs new business card

Our nearly 20 year old custom software development company would like to better include the fact that we are now providing Bitcoin services. These new services are B2B include education (how to acquire and securely hold Bitcoin) and integrating Bitcoin payments into existing ecommerce sites or other existing systems. Please keep the card clean and simple. Attached is our current design and some other files. vextorial.com

Target Market(s)

businesses owners interested in long term relationship

Industry/Entity Type

Custom software development and Bitcoin

Contact Information for Business Card

Dale Parker, dale@vextorial.com, vextorial.com, (888) 555-VXTRL

Font styles to use
Other font styles liked:
• monospace

Requirements
Must have
• double-sided
Nice to have
• clean and simple
Should not have
• physical address

```html
<!DOCTYPE html>
<html lang="en">
<head>
<meta charset="utf-8">
<title>Vextorial Business Card</title>
<link href="https://fonts.googleapis.com/css2?family=Source+Sans+3:wght@400;600;700&display=swap" rel="stylesheet">
<style>
  :root {
    --backdrop: #1d1d1d;
    --card-white: #ffffff;
    --brand-blue: #3d72b8;
    --accent-orange: #f27e22;
    --text-light: #ffffff;
    --text-soft: rgba(255, 255, 255, 0.82);
    --font-main: "Source Sans 3", "Source Sans Pro", sans-serif;
  }
  * { margin: 0; padding: 0; box-sizing: border-box; }
  html, body {
    width: 1200px;
    height: 1200px;
    overflow: hidden;
    background: var(--backdrop);
    font-family: var(--font-main);
  }
  .canvas {
    position: relative;
    width: 1200px;
    height: 1200px;
  }
  .card {
    position: absolute;
    left: 250px;
    width: 700px;
    height: 400px;
    border-radius: 22px;
    overflow: hidden;
  }
  .card-front {
    top: 170px;
    background: var(--card-white);
  }
  .card-back {
    top: 631px;
    background: var(--brand-blue);
  }
  .front-band {
    position: absolute;
    left: 0;
    top: 81px;
    width: 100%;
    height: 236px;
    background: var(--brand-blue);
  }
  .front-brand {
    position: absolute;
    left: 34px;
    top: 96px;
    font-size: 34px;
    font-weight: 700;
    letter-spacing: 1px;
    color: var(--text-light);
  }
  .contact-block {
    position: absolute;
    left: 373px;
    top: 36px;
    color: var(--text-light);
  }
  .person-name {
    font-size: 30px;
    font-weight: 700;
    letter-spacing: 1.5px;
    line-height: 1;
    text-transform: uppercase;
  }
  .person-title {
    margin-top: 6px;
    font-size: 19px;
    font-weight: 400;
    letter-spacing: 0.5px;
  }
  .contact-list {
    list-style: none;
    margin-top: 20px;
  }
  .contact-item {
    display: flex;
    align-items: center;
    height: 25px;
    font-size: 17px;
    letter-spacing: 0.5px;
  }
  .contact-icon {
    width: 15px;
    height: 15px;
    margin-right: 11px;
    flex: none;
  }
  .back-brand {
    position: absolute;
    left: 0;
    top: 124px;
    width: 100%;
    text-align: center;
    color: var(--text-light);
  }
  .back-wordmark {
    font-size: 84px;
    font-weight: 700;
    line-height: 1;
    letter-spacing: 1px;
  }
  .back-tagline {
    margin-top: 12px;
    font-size: 30px;
    font-weight: 400;
    letter-spacing: -1px;
  }
  .back-services {
    position: absolute;
    left: 0;
    bottom: 46px;
    width: 100%;
    text-align: center;
    font-size: 17px;
    font-weight: 600;
    letter-spacing: 1.5px;
    color: var(--text-soft);
  }
  .service-dot {
    display: inline-block;
    width: 6px;
    height: 6px;
    margin: 0 12px 3px;
    border-radius: 50%;
    background: var(--accent-orange);
  }
</style>
</head>
<body>
<main class="canvas">
  <section class="card card-front" aria-label="Card front">
    <div class="front-band">
      <div class="front-brand">VEXTORIAL</div>
      <div class="contact-block">
        <h1 class="person-name">Dale Parker</h1>
        <p class="person-title">Founding Partner</p>
        <ul class="contact-list">
          <li class="contact-item">
            <svg class="contact-icon" viewBox="0 0 16 16" aria-hidden="true">
              <path d="M3.5 1.5l2.5 3-1.5 2c.8 1.8 2.2 3.2 4 4l2-1.5 3 2.5-1.8 2.3C6.5 13.5 2.5 9.5 1.2 3.3z" fill="#fff"/>
              <path d="M9.5 1.8a5 5 0 0 1 4.7 4.7M9.3 4.2a2.6 2.6 0 0 1 2.5 2.5" stroke="#fff" stroke-width="1.3" fill="none"/>
            </svg>
            (888) 555-VXTRL
          </li>
          <li class="contact-item">
            <svg class="contact-icon" viewBox="0 0 16 16" aria-hidden="true">
              <rect x="1" y="3.5" width="14" height="9.5" fill="#fff"/>
              <path d="M1 3.5l7 5.5 7-5.5" stroke="#3d72b8" stroke-width="1.2" fill="none"/>
            </svg>
            dale@vextorial.com
          </li>
          <li class="contact-item">
            <svg class="contact-icon" viewBox="0 0 16 16" aria-hidden="true">
              <circle cx="8" cy="8" r="7" fill="#fff"/>
              <path d="M4 4.5c1.5 0 2 1 3 1.5s.5 2-.5 2.5-1 2-.5 3.5M10 3c.5 1.5 2 1.5 3 2.5M10.5 9.5c1 0 2 .8 1.5 2.5" stroke="#3d72b8" stroke-width="1.4" fill="none"/>
            </svg>
            vextorial.com
          </li>
        </ul>
      </div>
    </div>
  </section>

  <section class="card card-back" aria-label="Card back">
    <div class="back-brand">
      <div class="back-wordmark">VEXTORIAL</div>
      <p class="back-tagline">developer of custom applications</p>
    </div>
    <p class="back-services">BITCOIN EDUCATION<span class="service-dot"></span>BITCOIN PAYMENT INTEGRATION</p>
  </section>
</main>
</body>
</html>
```